Business Card Design

We need a design for business cards for our company. We have a logo. We teach EMT's and we are based out of Virginia. The information that will need to add would be, name, title, phone number, email, address. On the back of the business card would be "We help you, help others"

Target Market(s)

People that want to become EMT's

Colors

Designer to choose colors to be used in the design.

Requirements
Must have
• company logo

```html
<!DOCTYPE html>
<html lang="en">
<head>
<meta charset="utf-8">
<title>Rescue Path Academy – Business Card</title>
<link rel="stylesheet" href="https://fonts.googleapis.com/css2?family=Montserrat:wght@600&family=Work+Sans:wght@400;500&display=swap">
<style>
  :root {
    --stage: #2b2b2d;
    --navy: #1f2a35;
    --paper: #ffffff;
    --red: #c8102e;
    --grey: #7a7d82;
    --pale: #f8eef0;
  }
  * { box-sizing: border-box; margin: 0; padding: 0; }
  html, body { width: 1200px; height: 878px; overflow: hidden; }
  body {
    position: relative;
    background: var(--stage);
    font-family: "Work Sans", sans-serif;
  }
  .card {
    position: absolute;
    width: 620px;
    height: 354px;
    overflow: hidden;
    box-shadow: 0 14px 30px rgba(0,0,0,.45);
  }
  .card-back { left: 80px; top: 60px; background: var(--navy); }
  .card-front { left: 500px; top: 464px; background: var(--paper); }

  .brand {
    display: flex;
    align-items: center;
    gap: 10px;
    font-family: "Montserrat", sans-serif;
    font-weight: 600;
    color: var(--red);
    text-transform: uppercase;
    letter-spacing: 1px;
  }
  .brand-dot {
    width: 14px; height: 14px;
    border-radius: 50%;
    background: var(--red);
    flex: none;
  }
  .card-back .brand {
    position: absolute;
    left: 50%; top: 50%;
    transform: translate(-50%, -50%);
    font-size: 30px;
    white-space: nowrap;
  }
  .card-back .brand-dot { width: 20px; height: 20px; }
  .card-front .brand {
    position: absolute;
    left: 30px; top: 28px;
    font-size: 19px;
  }

  .decor {
    position: absolute;
    left: 330px; top: 40px;
    width: 250px; height: 300px;
    background: linear-gradient(180deg, var(--pale), #f4f4f4);
  }
  .divider {
    position: absolute;
    left: 36px; top: 214px;
    width: 548px; height: 1.5px;
    background: var(--red);
  }
  .accent-bar {
    position: absolute;
    right: 0; top: 150px;
    width: 10px; height: 50px;
    background: var(--red);
  }
  .person {
    position: absolute;
    right: 40px; top: 148px;
    text-align: right;
  }
  .person-name {
    font-family: "Montserrat", sans-serif;
    font-weight: 600;
    font-size: 24px;
    letter-spacing: 1.5px;
    color: var(--red);
    text-transform: uppercase;
  }
  .person-title {
    font-size: 15px;
    color: var(--grey);
    margin-top: 2px;
    letter-spacing: .5px;
  }
  .contacts {
    position: absolute;
    left: 36px; top: 232px;
    list-style: none;
    font-size: 16px;
    color: var(--grey);
    letter-spacing: .5px;
  }
  .contacts li {
    display: flex;
    align-items: center;
    gap: 8px;
    line-height: 26px;
  }
  .contacts svg { width: 13px; height: 13px; flex: none; }
  .contacts .web-name { color: var(--red); font-weight: 500; }
  .address {
    position: absolute;
    right: 40px; bottom: 34px;
    text-align: right;
    font-size: 16px;
    line-height: 24px;
    color: var(--grey);
    letter-spacing: .8px;
    font-style: normal;
  }
</style>
</head>
<body>

<section class="card card-back" aria-label="Card back">
  <div class="brand"><span class="brand-dot"></span>Rescue Path Academy</div>
</section>

<section class="card card-front" aria-label="Card front">
  <div class="decor" role="img" aria-label="Faint medical cross with heartbeat line decoration"></div>
  <div class="brand"><span class="brand-dot"></span>Rescue Path Academy</div>

  <div class="person">
    <p class="person-name">Daniel Hart</p>
    <p class="person-title">Director</p>
  </div>
  <div class="accent-bar"></div>
  <div class="divider"></div>

  <ul class="contacts">
    <li>
      <svg viewBox="0 0 16 16" aria-hidden="true"><path d="M4 1l3 3-2 2c1 2 3 4 5 5l2-2 3 3-2 2C7 14 2 9 2 3z" fill="#c8102e"/></svg>
      555-014-2270
    </li>
    <li>
      <svg viewBox="0 0 16 16" aria-hidden="true"><rect x="1.5" y="3.5" width="13" height="9" fill="none" stroke="#c8102e" stroke-width="1.5"/><path d="M1.5 3.5l6.5 5 6.5-5" fill="none" stroke="#c8102e" stroke-width="1.5"/></svg>
      info@rescuepath.com
    </li>
    <li>
      <svg viewBox="0 0 16 16" aria-hidden="true"><circle cx="8" cy="8" r="6.5" fill="none" stroke="#c8102e" stroke-width="1.5"/><path d="M1.5 8h13M8 1.5c-3 3.5-3 9.5 0 13M8 1.5c3 3.5 3 9.5 0 13" fill="none" stroke="#c8102e" stroke-width="1.2"/></svg>
      <span>www.<span class="web-name">rescuepath</span>.com</span>
    </li>
  </ul>

  <address class="address">128 Linden Ave.<br>Fairview, VA 24401</address>
</section>

</body>
</html>
```